Business card for a new innovative and professional lawn care business

We need a business card design for a new lawn care business in Halifax NS Canada. We offer lawn services in Halifax & Bedford. Our services offered include lawn care, garden services, and property maintenance. We take pride in our work and are experienced at what we do. I would like to see a design that is double sided. On the backside I would like the something simple (maybe my logo preferably on blackround (linked below) with website link, Facebook page or something). The front I want to include contact info:
Morgan Pell
phone 902-555-0148
email - brookvaleyards.ca
facebook - Facebook.com/brookvaleyards
Instagram maybe ? - instagram.com/brookvaleyard
Serving Halifax and Bedford for 5 years?
I don't want it to have too much information as I will be passing them out in aim to visit website, or call !
We do want it to include lawn care, garden services and property maintenance.
Basic, catchy, and modern looking !
Logo attached below !

Target Market(s)

Passing business cards to everyone I meet or interact with.

Industry/Entity Type

Lawn Care

Contact Information for Business Card

Double sided with some basic information, with catchy colours and easy to look at.

Font styles to use
Sans Serif

Requirements
Must have
• Must be double sided and have :
• Name, Phone, Email, FB, Website, and 3 main services offered - lawn care, property maintenance, garden services
Nice to have
• Would be nice to have instagram link if it goes well on there
Should not have
• Don't want too much writing or images that are distracting

```html
<!DOCTYPE html>
<html lang="en">
<head>
<meta charset="utf-8">
<title>Brookvale Yards – Business Card</title>
<link href="https://fonts.googleapis.com/css2?family=Source+Sans+3:ital,wght@0,400;0,700;1,400&display=swap" rel="stylesheet">
<style>
  :root {
    --backdrop: #4a423e;
    --card: #121212;
    --green-bright: #5cc531;
    --green-deep: #2a9a3e;
    --text-light: #e9e9e9;
    --divider: #8a8a8a;
  }
  * { margin: 0; padding: 0; box-sizing: border-box; }
  html, body {
    width: 1200px; height: 814px; overflow: hidden;
    background: var(--backdrop);
    font-family: "Source Sans 3", sans-serif;
  }
  .sheet {
    position: relative; width: 1200px; height: 814px;
    display: flex; align-items: center; justify-content: center; gap: 50px;
  }
  .card {
    position: relative; width: 540px; height: 310px;
    background: var(--card);
    box-shadow: 0 10px 24px rgba(0,0,0,.45);
  }
  /* Front */
  .brand {
    position: absolute; left: 120px; top: 62px;
    display: flex; align-items: center; gap: 12px;
  }
  .brand-dot { width: 22px; height: 22px; border-radius: 50%; background: var(--green-deep); }
  .brand-name {
    font-weight: 700; font-size: 40px; letter-spacing: 1px;
    color: var(--green-bright); text-transform: uppercase; line-height: 1;
  }
  .identity {
    position: absolute; right: 300px; top: 196px; text-align: right;
  }
  .identity-name { font-weight: 700; font-size: 22px; color: var(--green-bright); line-height: 1.2; }
  .identity-email { font-style: italic; font-size: 18px; color: var(--text-light); }
  .divider {
    position: absolute; left: 256px; top: 168px; width: 1px; height: 100px;
    background: var(--divider);
  }
  .contacts {
    position: absolute; left: 272px; top: 166px; list-style: none;
  }
  .contacts li {
    display: flex; align-items: center; gap: 8px;
    font-size: 16px; color: var(--text-light); line-height: 25px;
  }
  .contacts svg { width: 14px; height: 14px; flex: none; }
  .icon-box { width: 13px; height: 13px; background: var(--green-bright); border-radius: 2px; flex: none; }
  /* Back */
  .back-mark {
    position: absolute; left: 0; right: 0; top: 92px;
    display: flex; justify-content: center; align-items: center; gap: 14px;
  }
  .back-mark .brand-dot { width: 30px; height: 30px; }
  .back-mark .brand-name { color: var(--green-deep); font-size: 44px; }
  .services {
    position: absolute; left: 0; right: 0; bottom: 44px;
    display: flex; justify-content: center; align-items: center; gap: 6px;
    font-size: 15px; color: var(--text-light);
  }
  .services svg { width: 13px; height: 13px; }
</style>
</head>
<body>
<main class="sheet">
  <section class="card card-front" aria-label="Card front">
    <div class="brand">
      <span class="brand-dot"></span>
      <span class="brand-name">Brookvale Yards</span>
    </div>
    <div class="identity">
      <p class="identity-name">Morgan Pell</p>
      <p class="identity-email">info@brookvaleyards.ca</p>
    </div>
    <div class="divider"></div>
    <ul class="contacts">
      <li>
        <svg viewBox="0 0 24 24"><path fill="#e9e9e9" d="M6.6 10.8a15.1 15.1 0 0 0 6.6 6.6l2.2-2.2c.3-.3.7-.4 1-.2 1.1.4 2.3.6 3.6.6.6 0 1 .4 1 1V20c0 .6-.4 1-1 1A17 17 0 0 1 3 4c0-.6.4-1 1-1h3.5c.6 0 1 .4 1 1 0 1.3.2 2.5.6 3.6.1.3 0 .7-.2 1z"/></svg>
        902-555-0148
      </li>
      <li>
        <svg viewBox="0 0 24 24"><circle cx="12" cy="12" r="10" fill="none" stroke="#5cc531" stroke-width="2.4"/><path d="M2 12h20M12 2c3 3 3 17 0 20M12 2c-3 3-3 17 0 20" fill="none" stroke="#5cc531" stroke-width="2"/></svg>
        brookvaleyards.ca
      </li>
      <li><span class="icon-box"></span>brookvaleyards</li>
      <li><span class="icon-box"></span>brookvaleyard</li>
    </ul>
  </section>

  <section class="card card-back" aria-label="Card back">
    <div class="back-mark">
      <span class="brand-dot"></span>
      <span class="brand-name">Brookvale Yards</span>
    </div>
    <p class="services">
      Lawn Care
      <svg viewBox="0 0 24 24"><path d="M3 13l6 6L21 5" fill="none" stroke="#5cc531" stroke-width="4"/></svg>
      Property Maintenance
      <svg viewBox="0 0 24 24"><path d="M3 13l6 6L21 5" fill="none" stroke="#5cc531" stroke-width="4"/></svg>
      Garden Services
    </p>
  </section>
</main>
</body>
</html>
```